Marta's Dwellings website

We need a simple website for our property investment business in the UK. We basically need our contact details and brief description.We have the company logo already done (via ArtFlockly) so please use these:https://drive.google.com/drive/folders/1szJ3iRhelElZ40NIFT7w-c14MaY3Y_oV?usp=sharingYou could use some stock photos of UK houses for now.Let me know when to provide more detailed descriptions, etc

Coding

Coded - Design and coding required

Number of Pages Required

1 page

Colors

Designer to choose colors to be used in the design.

```html
<!DOCTYPE html>
<html lang="en">
<head>
<meta charset="utf-8">
<title>Marta's Dwellings</title>
<link href="https://fonts.googleapis.com/css2?family=Jost:wght@300;400;500&family=Open+Sans:ital,wght@0,400;0,600;0,700;1,400&display=swap" rel="stylesheet">
<style>
:root{
  --ink:#1e1e1e;
  --text:#555;
  --muted:#777;
  --light:#f3f3f3;
  --band:#e8e8e8;
  --dark:#2a2a2a;
  --topbar:#141414;
  --white:#fff;
  --accent:#9a8ac0;
  --line:#cfcfcf;
}
*{box-sizing:border-box;margin:0;padding:0}
html,body{width:1200px;height:4373px;overflow:hidden;background:var(--white)}
body{font-family:"Open Sans",Arial,sans-serif;color:var(--text);position:relative}
section,header,footer{position:relative;width:1200px}
.abs{position:absolute}
.heading{font-family:"Jost",sans-serif;font-weight:300;color:var(--ink);text-transform:uppercase;letter-spacing:1px}
.center{left:0;width:1200px;text-align:center}
.mark{position:absolute;left:564px;width:72px;height:6px;background:var(--ink)}

/* top bar */
.topbar{height:37px;background:var(--topbar);color:#eee;font-size:13px;text-align:center;line-height:37px}
.topbar svg{vertical-align:-2px;margin-right:6px}

/* hero */
.hero{height:661px;background:linear-gradient(180deg,#9a9893 0%,#857c73 22%,#6d5646 45%,#5b4334 70%,#3f2f26 100%)}
.hero .shade{position:absolute;inset:0;background:rgba(20,15,10,.25)}
.brand{left:110px;top:70px;width:300px;text-align:center;color:var(--white);font-family:"Jost",sans-serif;font-weight:400;font-size:22px;letter-spacing:9px;text-transform:uppercase}
.brand .sq{display:block;width:70px;height:70px;border:3px solid var(--white);margin:0 auto 26px}
.nav{left:453px;top:80px;display:flex;gap:28px;font-family:"Jost",sans-serif;font-size:16px;color:var(--white);text-transform:uppercase}
.nav .active{border-top:2px solid var(--white);padding-top:7px;margin-top:-9px}
.hero-title{top:262px;font-family:"Jost",sans-serif;font-weight:300;font-size:78px;letter-spacing:9px;color:var(--white);text-transform:uppercase}
.hero-sub{top:382px;font-family:"Jost",sans-serif;font-weight:300;font-size:29px;color:var(--white)}
.btn-white{position:absolute;background:var(--white);color:var(--ink);font-weight:700;font-size:17px;text-align:center;text-transform:uppercase}
.dots{top:576px;display:flex;justify-content:center;gap:6px}
.dots i{width:16px;height:16px;border:2px solid var(--white);border-radius:50%;display:block}
.dots i.on{background:var(--white)}

/* welcome */
.welcome{height:931px}
.intro{left:210px;width:780px;top:294px;font-size:14px;line-height:28px;text-align:center;color:var(--muted)}
.feature{width:463px;height:116px;background:var(--light);padding:16px 20px 0 98px}
.feature svg{position:absolute;left:24px;top:20px}
.feature h3{font-family:"Jost",sans-serif;font-weight:400;font-size:22px;color:var(--ink);margin-bottom:8px}
.feature p{font-size:13px;line-height:25px;color:var(--muted)}

/* track record */
.record{height:482px;background:var(--band)}
.stat{top:250px;width:306px;height:130px;background:var(--white);box-shadow:0 1px 3px rgba(0,0,0,.08);display:flex;align-items:center;padding-left:28px;gap:30px}
.stat b{font-family:"Jost",sans-serif;font-weight:500;font-size:48px;color:var(--ink)}
.stat span{font-family:"Jost",sans-serif;font-size:21px;line-height:33px;color:var(--text)}

/* about */
.about{height:606px}
.about h2{left:112px;top:140px;font-size:44px;line-height:58px;text-align:left}
.about p{left:112px;top:292px;width:485px;font-size:14px;line-height:32px;color:var(--muted)}
.btn-outline{left:112px;top:450px;width:129px;height:48px;border:2px solid #bbb;font-size:14px;font-weight:700;color:var(--ink);text-align:center;line-height:44px}
.video{left:641px;top:122px;width:447px;height:316px;background:linear-gradient(135deg,#4a4640 0%,#a39a8e 40%,#e9e5dc 70%,#c9b79c 100%)}

/* testimonials */
.testi{height:665px;background:var(--band)}
.card{top:295px;width:308px;height:258px;background:var(--white);box-shadow:0 1px 4px rgba(0,0,0,.12);text-align:center;padding:62px 22px 0}
.avatar{position:absolute;left:112px;top:-42px;width:84px;height:84px;border-radius:50%;background:linear-gradient(160deg,#d9c2ae,#8a6c58);border:4px solid var(--white)}
.card q{display:block;font-style:italic;font-size:13px;line-height:25px;color:var(--muted);quotes:"\201C" "\201D"}
.card h4{font-weight:600;font-size:18px;color:var(--ink);margin-top:18px}
.card small{display:block;font-style:italic;font-size:13px;color:var(--accent);margin-top:6px}
.arrow{top:371px;width:46px;height:46px;border:2px solid #999;border-radius:50%;display:flex;align-items:center;justify-content:center}

/* advisors */
.advisors{height:480px;background:var(--dark)}
.advisors .mark{background:var(--white)}
.advisors p{top:220px;font-size:15px;line-height:33px;color:#ddd}

/* footer */
.footer{height:511px}
.footer .brand{color:var(--ink);left:112px;top:97px;width:326px;font-size:22px}
.footer .brand .sq{border-color:var(--ink)}
.faddr{left:112px;top:292px;width:340px;font-size:13px;line-height:28px;color:var(--muted);padding-left:22px}
.faddr svg{position:absolute;left:0;top:7px}
.fhead{font-family:"Jost",sans-serif;font-size:22px;color:var(--ink)}
.links{left:530px;top:183px;list-style:none;font-size:13px;line-height:31px;color:var(--muted)}
.news{left:721px;top:222px;width:330px;font-size:14px;line-height:27px;color:var(--muted)}
.email{left:723px;top:253px;width:224px;height:45px;border:1px solid #999;font-size:14px;color:var(--muted);line-height:43px;padding-left:40px}
.email svg{position:absolute;left:16px;top:15px}
.signup{left:947px;top:253px;width:92px;height:45px;background:var(--ink);color:var(--white);font-weight:700;font-size:14px;text-align:center;line-height:45px;text-transform:uppercase}
.divider{left:112px;top:396px;width:976px;height:1px;background:var(--line)}
.copy{left:112px;top:445px;font-size:13px;color:var(--text)}
.social{left:877px;top:430px;display:flex;gap:7px}
.social i{display:block;width:48px;height:48px;border:2px solid #444;border-radius:50%}
</style>
</head>
<body>

<div class="topbar"><svg width="11" height="14" viewBox="0 0 11 14"><path d="M5.5 0A5.5 5.5 0 0 0 0 5.5C0 9.5 5.5 14 5.5 14S11 9.5 11 5.5A5.5 5.5 0 0 0 5.5 0Zm0 7.7a2.2 2.2 0 1 1 0-4.4 2.2 2.2 0 0 1 0 4.4Z" fill="#eee"/></svg>Unit 8, Larkfield Court, 14-16 Orchard Row, Ashby Vale, Leicestershire, United Kingdom, LE9 4QT</div>

<header class="hero" role="img" aria-label="Aerial view of UK terraced houses and red roofs at dusk">
  <div class="shade"></div>
  <div class="abs brand"><span class="sq"></span>Marta's Dwellings</div>
  <nav class="abs nav">
    <span class="active">Home</span><span>About Us</span><span>Portfolio</span><span>Investors</span><span>Agents</span><span>Contact Us</span>
    <svg width="16" height="16" viewBox="0 0 16 16"><circle cx="6.5" cy="6.5" r="5" fill="none" stroke="#fff" stroke-width="2"/><path d="M10.3 10.3 15 15" stroke="#fff" stroke-width="2.4"/></svg>
  </nav>
  <h1 class="abs center hero-title">Marta's Dwellings</h1>
  <p class="abs center hero-sub">We are a property investment business in the UK</p>
  <div class="btn-white" style="left:506px;top:419px;width:188px;height:58px;line-height:58px">Get a Quote</div>
  <div class="abs center dots"><i class="on"></i><i></i><i></i><i></i></div>
</header>

<section class="welcome">
  <div class="mark" style="top:130px"></div>
  <h2 class="abs center heading" style="top:170px;font-size:44px">Welcome to Marta's Dwellings</h2>
  <p class="abs intro">Nam libero tempore, cum soluta nobis est eligendi optio cumque nihil impedit quo minus id quod maxime placeat facere possimus, omnis voluptas assumenda est, omnis d bus autem quibusdam et aut officiis debitis aut rerum necessitatibus saepe eveniet ut et voluptates repudiandae sint et molestiae.</p>

  <div class="abs feature" style="left:112px;top:393px">
    <svg width="44" height="50" viewBox="0 0 44 50" fill="none" stroke="#777" stroke-width="2"><circle cx="22" cy="14" r="11"/><path d="M2 48c0-12 9-20 20-20s20 8 20 20Z"/></svg>
    <h3>Investment Philosophy</h3><p>At vero eos et accusamus et iusto odio dignissimos ducimus qui blanditiis praesentiu ccus.</p>
  </div>
  <div class="abs feature" style="left:624px;top:393px">
    <svg width="40" height="52" viewBox="0 0 40 52" fill="none" stroke="#777" stroke-width="2"><path d="M20 2a16 16 0 0 0-9 29v8h18v-8A16 16 0 0 0 20 2Z"/><path d="M13 44h14M15 49h10"/></svg>
    <h3>Neighborhood Insights</h3><p>At vero eos et accusamus et iusto odio dignissimos ducimus qui blanditiis praesentiu ccus.</p>
  </div>
  <div class="abs feature" style="left:112px;top:539px">
    <svg width="58" height="54" viewBox="0 0 58 54" fill="none" stroke="#777" stroke-width="2"><circle cx="29" cy="14" r="9"/><circle cx="10" cy="18" r="7"/><circle cx="48" cy="18" r="7"/><path d="M14 52c0-12 7-20 15-20s15 8 15 20Z"/><path d="M1 44c0-8 4-14 10-14M57 44c0-8-4-14-10-14"/></svg>
    <h3>Local Partnerships</h3><p>At vero eos et accusamus et iusto odio dignissimos ducimus qui blanditiis praesentiu ccus.</p>
  </div>
  <div class="abs feature" style="left:624px;top:539px">
    <svg width="54" height="44" viewBox="0 0 54 44" fill="none" stroke="#777" stroke-width="2"><path d="M2 2v40h50"/><rect x="10" y="24" width="6" height="14"/><rect x="20" y="16" width="6" height="22"/><rect x="30" y="20" width="6" height="18"/><rect x="40" y="8" width="6" height="30"/></svg>
    <h3>Market Overview</h3><p>At vero eos et accusamus et iusto odio dignissimos ducimus qui blanditiis praesentiu ccus.</p>
  </div>
  <div class="abs feature" style="left:112px;top:685px">
    <svg width="56" height="44" viewBox="0 0 56 44" fill="none" stroke="#777" stroke-width="2"><path d="M2 2v40h52"/><path d="M8 34l12-12 8 8 18-18"/><path d="M38 10h9v9"/></svg>
    <h3>Compelling Niche</h3><p>At vero eos et accusamus et iusto odio dignissimos ducimus qui blanditiis praesentiu ccus.</p>
  </div>
  <div class="abs feature" style="left:624px;top:685px">
    <svg width="48" height="46" viewBox="0 0 48 46" fill="none" stroke="#777" stroke-width="2"><rect x="2" y="10" width="32" height="32" rx="4"/><path d="M18 30l2-8 20-20 6 6-20 20Z"/></svg>
    <h3>Property Analysis</h3><p>At vero eos et accusamus et iusto odio dignissimos ducimus qui blanditiis praesentiu ccus.</p>
  </div>
</section>

<section class="record">
  <div class="mark" style="top:104px"></div>
  <h2 class="abs center heading" style="top:144px;font-size:44px">Our Track Record</h2>
  <div class="abs stat" style="left:112px"><b>45</b><span>Real<br>Estate<br>Investments</span></div>
  <div class="abs stat" style="left:446px"><b>70</b><span>Income<br>Generating<br>Properties</span></div>
  <div class="abs stat" style="left:782px;gap:14px"><b>$1.5B</b><span>Assets<br>Under<br>Management</span></div>
</section>

<section class="about">
  <div class="abs" style="left:112px;top:100px;width:72px;height:6px;background:var(--ink)"></div>
  <h2 class="abs heading">About<br>Marta's Dwellings</h2>
  <p class="abs">Nam libero tempore, cum soluta nobis est eligendi optio cumquenihil imp edit quo minus id quod maxime placeat facere possimus, omnivo luptas assumenda est, omnis dolor repellendus. Temporibus autequ ibusdamaut officiis debitis aut rerum necessi.</p>
  <div class="abs btn-outline">READ MORE</div>
  <div class="abs video" role="img" aria-label="Video still: business handshake over property documents with a small wooden house model">
    <svg class="abs" style="left:192px;top:127px" width="62" height="62" viewBox="0 0 62 62"><circle cx="31" cy="31" r="31" fill="#1e1e1e"/><path d="M24 18v26l21-13Z" fill="#fff"/></svg>
  </div>
</section>

<section class="testi">
  <div class="mark" style="top:106px"></div>
  <h2 class="abs center heading" style="top:146px;font-size:44px">Client Testimonials</h2>
  <div class="abs arrow" style="left:23px"><svg width="12" height="18" viewBox="0 0 12 18"><path d="M10 2 3 9l7 7" fill="none" stroke="#888" stroke-width="2"/></svg></div>
  <div class="abs card" style="left:98px"><div class="avatar" role="img" aria-label="Client portrait"></div><q>Nam libero tempore, cum soluta nobis est eligendi optio cumque nihil impedit quo minus id quod maxime placeat facere possi mus, omqumnis volup</q><h4>Lucien Moreau</h4><small>Propriétaire - Moreau Studio</small></div>
  <div class="abs card" style="left:446px"><div class="avatar" role="img" aria-label="Client portrait"></div><q>Nam libero tempore, cum soluta nobis est eligendi optio cumque nihil impedit quo minus id quod maxime placeat facere possi mus, omqumnis volup</q><h4>Camille Roux</h4><small>Propriétaire - Ivoire Voyages</small></div>
  <div class="abs card" style="left:794px"><div class="avatar" role="img" aria-label="Client portrait"></div><q>Nam libero tempore, cum soluta nobis est eligendi optio cumque nihil impedit quo minus id quod maxime placeat facere possi mus, omqumnis volup</q><h4>Étienne Varga</h4><small>Propriétaire - Atelier Lumen</small></div>
  <div class="abs arrow" style="left:1131px"><svg width="12" height="18" viewBox="0 0 12 18"><path d="M2 2l7 7-7 7" fill="none" stroke="#888" stroke-width="2"/></svg></div>
</section>

<section class="advisors">
  <div class="mark" style="top:86px"></div>
  <h2 class="abs center heading" style="top:126px;font-size:44px;color:var(--white)">Advisors Are Here to Help</h2>
  <p class="abs center">At vero eos et accusamus et iusto odio dignissimos ducimus qui blanditiis praesentium<br>voluptatum deleniti atque corrupt erunt mollitnobis este</p>
  <div class="btn-white" style="left:438px;top:309px;width:324px;height:63px;line-height:63px">Contact - Marta Louise Vane</div>
</section>

<footer class="footer">
  <div class="abs brand"><span class="sq"></span>Marta's Dwellings</div>
  <p class="abs faddr"><svg width="9" height="12" viewBox="0 0 11 14"><path d="M5.5 0A5.5 5.5 0 0 0 0 5.5C0 9.5 5.5 14 5.5 14S11 9.5 11 5.5A5.5 5.5 0 0 0 5.5 0Zm0 7.7a2.2 2.2 0 1 1 0-4.4 2.2 2.2 0 0 1 0 4.4Z" fill="#777"/></svg>Unit 8, Larkfield Court, 14-16 Orchard Row, Ashby Vale, Leicestershire, United Kingdom, LE9 4QT</p>
  <h3 class="abs fhead" style="left:530px;top:116px">Quick links</h3>
  <ul class="abs links"><li>Home</li><li>About Us</li><li>Portfolio</li><li>Investors</li><li>Agents</li><li>Contact Us</li></ul>
  <h3 class="abs fhead" style="left:721px;top:116px">Newsletter Subscription</h3>
  <p class="abs news" style="top:168px">Enter your email address to get information about us</p>
  <div class="abs email"><svg width="16" height="12" viewBox="0 0 16 12"><rect width="16" height="12" fill="#777"/><path d="M0 0l8 7 8-7" fill="none" stroke="#fff" stroke-width="1.5"/></svg>Email Address</div>
  <div class="abs signup">Sign Up!</div>
  <div class="abs divider"></div>
  <p class="abs copy">© 2019, Marta's Dwellings. All Rights Reserved.</p>
  <div class="abs social" aria-label="Social media links"><i></i><i></i><i></i><i></i></div>
</footer>

</body>
</html>
```